Cyber Security firm working in the Financial Services sector needs a brochure

We need a brochure covering our products and offerings. We work exclusively with Independent Broker Dealers, their Reps and RIAs in the US. We help them keep their computers secure and compliant with applicable regulations and policies. Have attached samples of our logo an descriptions of our products and services.

Target Market(s)

Financial Institutions and Financial Advisors

Industry/Entity Type

Financial Service

```html
<!DOCTYPE html>
<html lang="en">
<head>
<meta charset="utf-8">
<title>Ledgerline Secure – Services Brochure</title>
<link rel="stylesheet" href="https://fonts.googleapis.com/css2?family=Open+Sans:wght@400;600;700&display=swap">
<style>
  :root{
    --navy:#1d4b97;
    --navy-deep:#173f80;
    --sky:#3aa7dc;
    --mist:#e3e4e6;
    --paper:#ffffff;
    --ink:#3b3f45;
    --backdrop:#e9e9ea;
  }
  *{box-sizing:border-box;margin:0;padding:0}
  html,body{width:1200px;height:960px;overflow:hidden}
  body{background:var(--backdrop);font-family:"Open Sans",Arial,sans-serif;color:var(--ink)}
  .brochure{position:absolute;left:250px;top:24px;width:700px;height:912px;background:var(--paper);overflow:hidden;box-shadow:0 6px 24px rgba(0,0,0,.12)}
  .block{position:absolute}
  h2{font-weight:700;text-transform:uppercase;font-size:15px;line-height:1.1;letter-spacing:.2px;color:var(--navy);margin-bottom:6px}
  h3{font-weight:700;font-size:13.5px;color:#fff;margin:10px 0 4px}
  p{font-size:9.3px;line-height:1.38}
  ul{list-style:none;font-size:9.3px;line-height:1.38;padding-left:14px}
  ul li{position:relative}
  ul li::before{content:"";position:absolute;left:-10px;top:5px;width:4px;height:4px;border-radius:50%;background:#fff}

  .setup{left:0;top:0;width:420px;height:490px;background:var(--navy);color:#fff;padding:34px 26px 0 30px}
  .setup h2{color:#fff}
  .setup p{color:#e6ecf7;margin-bottom:12px}

  .services{left:420px;top:0;width:280px;height:600px;padding:40px 24px 0 24px}
  .services p{text-align:justify;margin-bottom:20px}

  .support{left:0;top:490px;width:446px;height:170px;padding:16px 24px 0 30px}
  .support p{text-align:justify}

  .email-bar{left:462px;top:606px;width:238px;height:48px;background:var(--navy-deep);color:#fff;display:flex;align-items:center;padding-left:16px;gap:10px;font-size:13px}
  .contact-strip{left:0;top:660px;width:462px;height:50px;background:var(--sky);color:#fff;display:flex;align-items:center;padding-left:28px;font-size:13px}
  .contact-item{display:flex;align-items:center;gap:10px}
  .contact-item + .contact-item{margin-left:36px}
  .icon{width:26px;height:26px;flex:none}

  .training{left:0;top:654px;width:700px;height:258px;background:var(--mist)}
  .training-band-left{left:0;top:660px;width:462px;height:252px;background:var(--mist)}
  .training-main{left:30px;top:726px;width:410px}
  .training-main p{text-align:justify;margin-bottom:10px}
  .training-side{left:474px;top:664px;width:212px}
  .training-side p{text-align:justify;margin-bottom:8px}
</style>
</head>
<body>
<main class="brochure">

  <section class="block setup">
    <h2>New Computer Sourcing</h2>
    <p>We are an authorized Norvane Value Added Reseller and will be happy to help you get your new computer. We work with you to determine an appropriate configuration and what would be a good fit for your specific needs.</p>

    <h2>New Computer Configuration</h2>
    <p>Configuration services provided for new computers. These can be sourced from us or locally and shipped to us or done remotely. Price $300.</p>

    <h3>Configure for Broker Dealer security requirements</h3>
    <ul>
      <li>Encrypt the Drive</li>
      <li>Set password Policy</li>
      <li>Set Screen saver timeout policy</li>
      <li>Apply all Operating System patches</li>
      <li>Set computer for Auto-update of all products where possible (if not subscribing to our Managed Software Patching service)</li>
      <li>Install default Anti-Virus software and configure to policy requirements (if not subscribing to our Managed Anti-Virus service)</li>
    </ul>

    <h3>Configure for functionality</h3>
    <ul>
      <li>Remove any unneeded software</li>
      <li>Configure browsers to function most reliably with BD sites</li>
      <li>Remove any unneeded Browser Plug-ins or Tool Bars</li>
      <li>Install Kova runtime (as required)</li>
      <li>Install Paperline Reader</li>
      <li>Install Brightdesk Office if needed – We can provide Office for $199</li>
    </ul>

    <h3>Safety</h3>
    <ul>
      <li>Create a System Image to an external encrypted drive</li>
      <li>Create Encryption Recovery media and keys if applicable</li>
    </ul>
  </section>

  <section class="block services">
    <h2>Internet Blocking<br>and Filtering</h2>
    <p>Comprehensive security for your network through award-winning phishing, botnet and malware site protection. Our web filtering service delivers network security services through the DNS layer blocking known malicious or infected sites from resolving on your network. This also allows you to block specific web sites and also broad categories of content from being accessed from your locations. A couple of examples might be Gambling and Pornography. $3.50 per month per device.</p>

    <h2>Firewall Sales</h2>
    <p>We provide pre-purchase consulting, configuration and support for business grade firewalls. We will help you spec an appropriate firewall, determine if VPN access is needed as well as any dedicated guest Wireless Access. The most suitable device for your location as well as any satellite locations is dependent on organization size and complexity. Prices starting at $750.</p>

    <h2>Public IP Monitoring</h2>
    <p>Knowing what the world sees of your front door to the internet is important. Our Public IP Monitoring scans your static IP address daily looking for inappropriate ports being made available over the internet. If we find your device has changes made we contact you to verify the changes were intentional and explain the ramifications of the changes. We don't want your network exposed because the Tech installing your new copier decided to open up a number of ports on your firewall. $100 per year per IP address.</p>
  </section>

  <section class="block support">
    <h2>General Computer Support</h2>
    <p>Ledgerline Secure has a long history of working with thousands of Independent Financial Advisors and Broker Dealers across the country. Because of this we have a lot of experience in supporting their technology needs. A benefit of this is we not only understand the technology but also the special needs of the financial services industry. All our technicians are US based, have years of industry experience and must pass a rigorous background check. We also understand your security requirements and will execute appropriate non-disclosure agreements to help you insure your information remains private. We've found we can resolve most software and configuration issues remotely. Our rates are $95 per hour.</p>
  </section>

  <div class="block training-band-left"></div>
  <div class="block training" style="left:462px;width:238px"></div>

  <div class="block email-bar">
    <svg class="icon" viewBox="0 0 26 26" aria-hidden="true"><circle cx="13" cy="13" r="12" fill="none" stroke="#fff" stroke-width="1.5"/><rect x="7" y="8.5" width="12" height="9" fill="#fff"/><path d="M7 8.5l6 5 6-5" fill="none" stroke="#173f80" stroke-width="1.2"/></svg>
    <span>info@ledgerlinesecure.com</span>
  </div>

  <div class="block contact-strip">
    <div class="contact-item">
      <svg class="icon" viewBox="0 0 26 26" aria-hidden="true"><circle cx="13" cy="13" r="12" fill="none" stroke="#fff" stroke-width="1.5"/><rect x="9" y="6.5" width="8" height="13" rx="4" fill="#fff"/><line x1="13" y1="7" x2="13" y2="11" stroke="#3aa7dc" stroke-width="1.2"/></svg>
      <span>www.ledgerlinesecure.com</span>
    </div>
    <div class="contact-item">
      <svg class="icon" viewBox="0 0 26 26" aria-hidden="true"><circle cx="13" cy="13" r="12" fill="none" stroke="#fff" stroke-width="1.5"/><path d="M9 7.5c-1.5 1-1.5 3 0 5.5s3.8 4.8 6 5.8c1.5.6 2.8 0 3.5-1l-2.4-2-1.4 1c-1.4-.8-2.8-2.3-3.5-3.8l1-1.3-2-2.6z" fill="#fff"/></svg>
      <span>555-014-2290</span>
    </div>
  </div>

  <section class="block training-main">
    <h2>Security Awareness Training</h2>
    <p>Security Awareness Training is a critical component of a comprehensive cyber security program. Because the cyber security environment is continuously changing, it is our experience that a multi-level approach is most effective in providing timely, actionable information as well as a firm grasp of critical security principals and requirements.</p>
    <p>Our first level is a targeted, electronic delivery of mini-training modules, typically taking no longer than 10 minutes to complete, every 4-6 weeks. These short, topical modules are designed to highlight current attacks and the appropriate response to the illustrated threat.</p>
  </section>

  <section class="block training-side">
    <p>The attacks are explained in an easy-to-understand format with the amount of technical jargon kept to the bare minimum. Each module presents several multiple choice questions to insure the respondent has a firm grasp of the topic. The continuous "drip" nature of this timely information is important in keeping security top-of-mind.</p>
    <p>Our second level provides periodic phishing emails. The emails consist of both general phishing emails, spear phishing, as well as very targeted "whaling" types of email. Anyone found susceptible to opening specially crafted attachments or links will be immediately taken to an on-line refresher course on how to spot fraudulent emails. $25 per user per year.</p>
  </section>

</main>
</body>
</html>
```